Pediatric Therapy Clinic Brochure

We need a Brochure for a new pediatric therapy clinic. The clinic offers occupational therapy, physical therapy, speech therapy and feeding therapy. We want a brochure for parents, doctors and medical professional. It should have a fun and inviting, but still professional feel. Should be kid focused, bright and colorful. All the text / wording is there and a rough layout. Now I need someone to tidy and jazz it up and make it look professional.

Target Market(s)

Parents, doctors, medical professional

Industry/Entity Type

Medical

Font styles to use
Serif
Sans Serif

Requirements
Must have
• Keep All the text with information about services the same. Logo on front. Pictures throughout (use any of the pictures provided) (try and match up with corresponding service) (pictures are labeled). Need to have Map and contact info
• Keep colors consistent with our logo
Nice to have
• Background, special effects. Make it look fancy and professional
Should not have
• Not so busy that is takes away from the text

```html
<!DOCTYPE html>
<html lang="en">
<head>
<meta charset="utf-8">
<title>Brightbrook Pediatric Therapy – Brochure Inside Spread</title>
<link href="https://fonts.googleapis.com/css2?family=Oswald:wght@500;600&family=Arimo:wght@400;700&display=swap" rel="stylesheet">
<style>
  :root{
    --navy:#1f2850;
    --navy-deep:#18203f;
    --blue:#163d94;
    --orange:#ee7a12;
    --orange-text:#e8641a;
    --yellow:#d8e21c;
    --lime:#bcd62a;
    --paper:#eef6f8;
    --bg:#8a8c90;
    --white:#ffffff;
  }
  *{box-sizing:border-box;margin:0;padding:0}
  html,body{width:1200px;height:1200px;overflow:hidden}
  body{background:var(--bg);font-family:"Arimo",Arial,sans-serif;position:relative}

  .brochure{position:absolute;left:30px;top:160px;width:1140px;height:880px;display:flex;box-shadow:0 18px 40px rgba(0,0,0,.3)}
  .panel{position:relative;width:380px;height:880px;overflow:hidden}
  .panel-shape{position:absolute;inset:0;width:100%;height:100%}

  .panel--ot{background:var(--navy)}
  .panel--speech{background:var(--paper)}
  .panel--feeding{background:var(--paper)}

  .photo{position:absolute;border:7px solid var(--orange);border-radius:22px;overflow:hidden}
  .photo--top{left:26px;top:34px;width:328px;height:180px;background:linear-gradient(135deg,#f4f1ec,#e8c8b4 55%,#d94b3c)}
  .photo--bottom{left:26px;top:668px;width:328px;height:178px;background:linear-gradient(120deg,#f3efe9,#d9b8a2 45%,#7a5a48 80%,#3a4a7a)}

  .service-title{font-family:"Oswald",Arial Narrow,sans-serif;font-weight:600;font-size:27px;letter-spacing:.2px;text-align:center;line-height:1.05}
  .service-lede{font-size:12.5px;line-height:1.3;text-align:center;margin-top:6px}
  .rule{height:3px;border-radius:2px;margin:10px 0 12px}

  .service-list{list-style:none;font-weight:700;font-size:13.2px;line-height:1.22}
  .service-list li{position:relative;padding-left:14px}
  .service-list li::before{content:"•";position:absolute;left:0;top:0}

  .panel--ot .block{position:absolute;left:28px;right:26px;top:232px;color:var(--white)}
  .panel--ot .service-title{color:var(--white)}
  .panel--ot .rule{background:var(--blue);height:4px}
  .panel--ot .service-list{color:var(--yellow);font-size:13.8px;line-height:1.28}

  .panel--speech .block,.panel--feeding .block{position:absolute;left:30px;right:30px}
  .panel--speech .service-title,.panel--feeding .service-title{color:var(--blue)}
  .panel--speech .service-lede,.panel--feeding .service-lede{color:var(--blue)}
  .panel--speech .rule,.panel--feeding .rule{background:var(--blue)}
  .panel--speech .service-list,.panel--feeding .service-list{color:var(--orange-text)}

  .block--speech{top:40px}
  .block--sensory{top:360px}
  .block--feeding{top:62px}
  .block--physical{top:322px}
  .block--group{top:600px}

  .brand{position:absolute;left:0;right:0;bottom:46px;display:flex;align-items:center;justify-content:center;gap:10px}
  .brand-dot{width:16px;height:16px;border-radius:50%;background:var(--orange)}
  .brand-name{font-family:"Arimo",Arial,sans-serif;font-weight:700;font-size:23px;color:var(--blue);line-height:1.05;text-align:left}

  .coming-soon{position:absolute;left:0;right:0;bottom:40px;text-align:center;color:var(--orange-text);font-size:14px;font-weight:400}
</style>
</head>
<body>
  <main class="brochure">

    <section class="panel panel--ot">
      <svg class="panel-shape" viewBox="0 0 380 880" preserveAspectRatio="none" aria-hidden="true">
        <path d="M0 0 H380 V70 C300 20 140 10 0 60 Z" fill="#f08a12"/>
        <path d="M0 0 H260 C170 18 80 30 0 58 Z" fill="#f7a21b"/>
        <path d="M0 660 C120 630 260 640 380 620 V880 H0 Z" fill="#18203f"/>
      </svg>
      <div class="photo photo--top" role="img" aria-label="Photo of a smiling child with paint-covered hands"></div>
      <div class="block">
        <h2 class="service-title">OCCUPATIONAL THERAPY</h2>
        <p class="service-lede">Helping children build better self-esteem, confidence and independence in all the things they do.</p>
        <div class="rule"></div>
        <ul class="service-list">
          <li>Sensory Processing Disorder</li>
          <li>Balance, Coordination, Strength, and Endurance</li>
          <li>Fine Motor and Handwriting</li>
          <li>Visual- Motor Integration</li>
          <li>Play and Social Skills</li>
          <li>Feeding and Oral Motor Skills</li>
          <li>Self-Care</li>
          <li>Academic and Cognitive Skills</li>
          <li>Behavioral Difficulties</li>
          <li>Developmental Delays</li>
        </ul>
      </div>
      <div class="photo photo--bottom" role="img" aria-label="Photo of three children sharing a whisper"></div>
    </section>

    <section class="panel panel--speech">
      <div class="block block--speech">
        <h2 class="service-title">SPEECH THERAPY</h2>
        <p class="service-lede">Helping children speak, communicate and understand language.</p>
        <div class="rule"></div>
        <ul class="service-list">
          <li>Expressive and Receptive Language</li>
          <li>Speech and Language Developmental Milestones</li>
          <li>Articulation / Intelligibility</li>
          <li>Speech Fluency</li>
          <li>Pragmatics and Social Skills</li>
          <li>Literacy and Vocabulary</li>
          <li>Apraxia of Speech</li>
          <li>Augmentative and Alternative Communication</li>
          <li>Feeding and Oral Motor</li>
        </ul>
      </div>
      <div class="block block--sensory">
        <h2 class="service-title">SENSORY INTEGRATION</h2>
        <p class="service-lede">Gradually increasing play based activities to improve a child's nervous system. Helping children learn to self-regulate their emotions, behaviors and arousal levels.</p>
        <div class="rule"></div>
        <ul class="service-list">
          <li>Autism and ADHD</li>
          <li>Sensory Processing Disorder</li>
          <li>Poor Tolerance of Sensory Stimuli from the Environment</li>
          <li>Meltdowns and Tantrums</li>
          <li>Poor Balance/Body Awareness</li>
          <li>Poor Attention and Concentration</li>
          <li>Poor Self-Regulation</li>
          <li>Behavior and Social Difficulties</li>
          <li>Poor Motor Coordination and Motor Planning</li>
          <li>Aggression, Frustration or Avoidance Behaviors</li>
        </ul>
      </div>
      <div class="brand">
        <span class="brand-dot"></span>
        <span class="brand-name">Brightbrook<br>Pediatric Therapy</span>
      </div>
    </section>

    <section class="panel panel--feeding">
      <svg class="panel-shape" viewBox="0 0 380 880" preserveAspectRatio="none" aria-hidden="true">
        <path d="M0 0 H380 V28 C230 10 80 40 0 150 Z" fill="#bcd62a"/>
        <path d="M0 880 V800 C120 790 150 720 300 700 C340 694 365 700 380 705 V880 Z" fill="#bcd62a"/>
      </svg>
      <div class="block block--feeding">
        <h2 class="service-title">FEEDING THERAPY</h2>
        <p class="service-lede">Providing skilled assessment and intervention to children with feeding difficulties.</p>
        <div class="rule"></div>
        <ul class="service-list">
          <li>Food Aversions</li>
          <li>Food Refusal</li>
          <li>Very Picky Eating</li>
          <li>Avoidance of Certain Textures</li>
          <li>Gagging and Vomiting</li>
          <li>Oral Motor/ Chewing Difficulties</li>
          <li>Limited Diet/Food Repertoire</li>
        </ul>
      </div>
      <div class="block block--physical">
        <h2 class="service-title">PHYSICAL THERAPY</h2>
        <p class="service-lede">Helping children move and interact within their environment smoothly and confidently.</p>
        <div class="rule"></div>
        <ul class="service-list">
          <li>Torticollis</li>
          <li>Walking and Mobility</li>
          <li>Developmental Motor Milestones</li>
          <li>Balance, Coordination, Motor Planning</li>
          <li>Strength, Muscle Tone and Range of Motion</li>
          <li>Sports Injuries</li>
          <li>Toe Walking</li>
          <li>Myofascial Release</li>
          <li>Postural Control and Positioning</li>
        </ul>
      </div>
      <div class="block block--group">
        <h2 class="service-title">GROUP THERAPY</h2>
        <p class="service-lede">Using peer role models to learn new and challenging skills.</p>
        <div class="rule"></div>
        <ul class="service-list">
          <li>Social Groups</li>
          <li>Feeding Groups</li>
        </ul>
      </div>
      <p class="coming-soon">**More Group Classes Coming Soon</p>
    </section>

  </main>
</body>
</html>
```